Electrician Letterhead Design MVR

We need some letterhead for our bills and other papers.
Customer address is on the right side (Swiss format)
A4 format

Design should also be applicable on Cards

Target Market(s)

Private Customers, Small Business

Industry/Entity Type

Electrician

Other font styles liked:
• incised 901

Colors
00AB8E
00BBA5
67D7C9
C6EFE9
E9F9F6

```html
<!DOCTYPE html>
<html lang="en">
<head>
<meta charset="utf-8">
<title>MVR Letterhead</title>
<link rel="stylesheet" href="https://fonts.googleapis.com/css2?family=Lato:wght@400;700;900&family=Montserrat:wght@500&family=Tangerine:wght@700&display=swap">
<style>
  :root {
    --teal: #00ab8e;
    --teal-soft: #67c9bc;
    --ink: #2b2b2b;
    --backdrop: #e6e8e8;
    --paper: #ffffff;
  }
  * { margin: 0; padding: 0; box-sizing: border-box; }
  html, body { width: 1200px; height: 1200px; overflow: hidden; background: var(--backdrop); }
  .letterhead {
    position: absolute; left: 205px; top: 27px; width: 790px; height: 1146px;
    background: var(--paper); box-shadow: 0 4px 18px rgba(0,0,0,.18);
    font-family: "Lato", sans-serif; color: var(--ink); overflow: hidden;
  }
  .brand { position: absolute; left: 62px; top: 40px; }
  .brand-name { font-weight: 900; font-size: 98px; line-height: 1; color: var(--teal); letter-spacing: -2px; }
  .brand-tagline { font-family: "Montserrat", sans-serif; font-weight: 500; font-size: 12px; color: var(--ink); margin-top: 4px; }
  .contact { position: absolute; left: 539px; top: 45px; padding-left: 10px; border-left: 1.5px solid var(--teal);
    font-family: "Montserrat", sans-serif; font-weight: 500; font-size: 13px; line-height: 18px; }
  .contact .address { margin-bottom: 8px; }
  .contact-row { display: flex; align-items: center; gap: 6px; line-height: 19.5px; }
  .contact-row svg { width: 11px; height: 11px; fill: var(--teal); }
  .letter { position: absolute; left: 62px; top: 262px; width: 668px; font-size: 14.5px; line-height: 18.5px; }
  .date { margin-bottom: 20px; }
  .recipient { margin-bottom: 19px; }
  .salutation { font-size: 19px; font-weight: 700; margin: 20px 0 16px; }
  .body p { text-align: justify; margin-bottom: 17px; font-size: 14px; line-height: 17.5px; }
  .closing { margin-top: 42px; font-size: 13.5px; }
  .signature { font-family: "Tangerine", cursive; font-size: 50px; line-height: 1; margin-top: 22px; color: #1d1d1d; }
  .footer { position: absolute; left: 0; bottom: 0; width: 790px; height: 55px; }
  .footer-url { position: absolute; right: 66px; bottom: 14px; color: #fff; font-family: "Montserrat", sans-serif;
    font-weight: 500; font-size: 18px; }
</style>
</head>
<body>
  <main class="letterhead">
    <header>
      <div class="brand">
        <div class="brand-name">MVR</div>
        <div class="brand-tagline">Elektrotechnik Moser GmbH</div>
      </div>
      <div class="contact">
        <div class="address">42 Lindenweg 7,<br>Talbrunn, 8404</div>
        <div class="contact-row">
          <svg viewBox="0 0 12 12"><path d="M2.5 1l2 2.3-1 1.3a7 7 0 0 0 3.9 3.9l1.3-1L11 9.5 9.6 11C5 11 1 7 1 2.4z"/></svg>052-318-4470
        </div>
        <div class="contact-row">
          <svg viewBox="0 0 12 12"><path d="M1 2.5h10v7H1z M1.3 2.8L6 6.5l4.7-3.7" stroke="#fff" stroke-width=".9"/></svg>hello@mvr-mail.com
        </div>
        <div class="contact-row">
          <svg viewBox="0 0 12 12"><circle cx="6" cy="6" r="5"/><path d="M1 6h10M6 1c-2.5 2.8-2.5 7.2 0 10M6 1c2.5 2.8 2.5 7.2 0 10" stroke="#fff" stroke-width=".8" fill="none"/></svg>www.mvr-elektro.com
        </div>
      </div>
    </header>

    <section class="letter">
      <p class="date">Feb-03-2022</p>
      <p class="recipient">Mr, Daniel Reed<br>President</p>
      <p class="recipient">Harbor Works Ltd<br>55 Mill Lane, Suite# 4<br>Town, Region, 340091</p>
      <p class="salutation">Dear Mr, Daniel</p>
      <div class="body">
        <p>Lorem ipsum dolor sit amet, consectetur adipisicing elit, sed do eiusmod tempor incididunt ut labore et dolore magna aliqua. Ut enim ad minim veniam, quis nostrud exercitation ullamco laboris nisi ut aliquip ex ea commodo consequat. Duis aute irure dolor in reprehenderit in voluptate velit esse cillum dolore eu fugiat nulla pariatur.</p>
        <p>Lorem ipsum dolor sit amet, consectetur adipisicing elit, sed do eiusmod tempor incididunt ut labore et dolore magna aliqua. Ut enim ad minim veniam, quis nostrud exercitation ullamco laboris nisi ut aliquip ex ea commodo consequat. Duis aute irure dolor in reprehenderit in voluptate velit esse cillum dolore eu fugiat nulla pariatur.</p>
        <p>Lorem ipsum dolor sit amet, consectetur adipisicing elit, sed do eiusmod tempor incididunt ut labore et dolore magna aliqua. Ut enim ad minim veniam, quis nostrud exercitation ullamco laboris nisi ut aliquip ex ea commodo consequat.</p>
        <p>Excepteur sint occaecat cupidatat non proident, sunt in culpa qui officia deserunt mollit anim id est laborum. re et dolore magnam aliquam quaerat voluptatem.</p>
      </div>
      <p class="closing">Regards</p>
      <p class="signature">Lukas Brenner</p>
    </section>

    <footer>
      <svg class="footer" viewBox="0 0 790 55" aria-hidden="true">
        <polygon points="0,28 438,28 425,55 0,55" fill="var(--teal-soft)"/>
        <polygon points="464,0 790,0 790,55 430,55" fill="var(--teal)"/>
      </svg>
      <div class="footer-url">www.mvr-elektro.com</div>
    </footer>
  </main>
</body>
</html>
```